Landscape Construction and Design Company

We are a landscape construction and design company from New Jersey. We design and install landscapes and hardscapes for residential properties. The name of the company is Belwick's Landscape and Design LLC. We specialize mostly in planting trees and stone work, some water features. We would like to see design themes that include a tree or trees and a stone walkway or wall. We like earth tone colors. We like traditional to modern designs.

Target Market(s)

Homeowners

Industry/Entity Type

Landscape

Contact Information for Business Card

Nature themed design, earth tone colors, space for company name, address, phone numbers, email and website address

Logo Text

No text

Font styles to use
Serif

Colors

Designer to choose colors to be used in the design.

Requirements
Must have
• A tree or trees, similar to the ones uploaded in my supporting images
Nice to have
• I like trees similar to those in my uploaded supporting images. I like artistic, nature theme, earth tone colors
Should not have
• Pictures of real landscapes, cartoon looking logo or objects

```html
<!DOCTYPE html>
<html lang="en">
<head>
<meta charset="utf-8">
<title>Belwick's Landscape and Design LLC – Business Cards</title>
<link href="https://fonts.googleapis.com/css2?family=Cinzel:wght@400&family=Lato:wght@400&display=swap" rel="stylesheet">
<style>
  :root {
    --backdrop: #999999;
    --maroon: #722a2c;
    --leaf: #6aa42e;
    --paper: #ffffff;
    --ink: #722a2c;
  }
  * { margin: 0; padding: 0; box-sizing: border-box; }
  html, body { width: 1200px; height: 900px; overflow: hidden; background: var(--backdrop); }
  .stage { position: relative; width: 1200px; height: 900px; }

  .card {
    position: absolute; top: 306px; width: 439px; height: 272px; overflow: hidden;
    box-shadow: 2px 3px 4px rgba(0,0,0,0.35);
  }
  .card--front { left: 150px; background: var(--paper); }
  .card--back { left: 609px; background: var(--maroon); }

  .corner-tabs { position: absolute; left: 0; top: 26px; }

  .person { position: absolute; left: 36px; top: 32px; }
  .person__name {
    font-family: "Cinzel", serif; font-size: 17px; color: var(--leaf); letter-spacing: 0.3px; line-height: 1;
  }
  .person__role {
    font-family: "Lato", sans-serif; font-size: 11px; color: var(--ink); margin-top: 4px; letter-spacing: 0.2px;
  }

  .brand-mark { position: absolute; width: 14px; height: 14px; background: var(--leaf); }
  .card--front .brand-mark { left: 196px; top: 127px; }
  .card--back .brand-mark { left: 70px; top: 113px; }

  .brand {
    position: absolute; font-family: "Lato", sans-serif; font-weight: 400; line-height: 1.3;
  }
  .card--front .brand { left: 218px; top: 122px; font-size: 19px; color: var(--ink); }
  .card--back .brand { left: 94px; top: 106px; font-size: 24px; color: var(--leaf); }

  .contact { position: absolute; left: 22px; top: 195px; list-style: none; }
  .contact__item {
    display: flex; align-items: center; gap: 6px; height: 17px;
    font-family: "Lato", sans-serif; font-size: 12px; color: var(--ink);
  }
  .contact__item:first-child { font-size: 13px; }
  .contact__icon { width: 10px; height: 10px; flex: none; }

  .address {
    position: absolute; right: 23px; top: 213px; text-align: right;
    font-family: "Lato", sans-serif; font-size: 11.5px; color: var(--ink); line-height: 15px; font-style: normal;
  }

  .base-band { position: absolute; left: 0; bottom: 0; }

  .services {
    position: absolute; left: 0; right: 0; top: 221px; text-align: center;
    font-family: "Lato", sans-serif; font-size: 13px; color: #ffffff; letter-spacing: 0.2px;
  }
</style>
</head>
<body>
<main class="stage">

  <section class="card card--front" aria-label="Business card front">
    <svg class="corner-tabs" width="30" height="38" viewBox="0 0 30 38" aria-hidden="true">
      <polygon points="0,0 11,0 16,37 0,37" fill="var(--maroon)"/>
      <polygon points="12,0 27,0 27,37 17,37" fill="var(--leaf)"/>
    </svg>

    <div class="person">
      <p class="person__name">DANIEL HARLOW</p>
      <p class="person__role">MANAGING DIRECTOR</p>
    </div>

    <span class="brand-mark" aria-hidden="true"></span>
    <p class="brand">Belwick's Landscape<br>and Design LLC</p>

    <ul class="contact">
      <li class="contact__item">
        <svg class="contact__icon" viewBox="0 0 10 10" aria-hidden="true"><path d="M1 3 Q5 0 9 3 L8 4.5 L6.5 3.8 L6.5 3 Q5 2.6 3.5 3 L3.5 3.8 L2 4.5 Z M2 5.5 H8 L9 9 H1 Z" fill="var(--leaf)"/></svg>
        444 555 7290
      </li>
      <li class="contact__item">
        <svg class="contact__icon" viewBox="0 0 10 10" aria-hidden="true"><rect x="0.5" y="2" width="9" height="6.5" fill="var(--leaf)"/><path d="M0.5 2 L5 5.6 L9.5 2" stroke="#fff" stroke-width="0.9" fill="none"/></svg>
        INFO@YOUREMAIL.COM
      </li>
      <li class="contact__item">
        <svg class="contact__icon" viewBox="0 0 10 10" aria-hidden="true"><circle cx="5" cy="5" r="4.5" fill="var(--leaf)"/><path d="M0.5 5 H9.5 M5 0.5 Q2.5 5 5 9.5 M5 0.5 Q7.5 5 5 9.5" stroke="#fff" stroke-width="0.7" fill="none"/></svg>
        WWW.WEBSITENAME.COM
      </li>
    </ul>

    <address class="address">421, ADDRESS LINE HERE<br>COUNTRY NAME,45452</address>

    <svg class="base-band" width="439" height="21" viewBox="0 0 439 21" aria-hidden="true">
      <polygon points="0,7 216,7 209,21 0,21" fill="var(--maroon)"/>
      <polygon points="224,0 439,0 439,21 206,21" fill="var(--leaf)"/>
    </svg>
  </section>

  <section class="card card--back" aria-label="Business card back">
    <span class="brand-mark" aria-hidden="true"></span>
    <p class="brand">Belwick's Landscape<br>and Design LLC</p>
    <p class="services">PLANTING TREES | STONE WORK | WATER FEATURES</p>
  </section>

</main>
</body>
</html>
```